Social Media Graphics - Oakline Push REVISED

Create 6-7 individual social media graphics (square size) to encourage folks to join our online course called:

The Harvest Ledger Circle
How to Launch a Multi-Million Business From Scratch
Sign Up Today!

IMPORTANT: Make the largest and most prominent text on the graphic be: How to Launch a Multi-Million Business From Scratch

For the color scheme of the graphics, let's try a blue color palette; make sure the graphics appeal to both men and women

Make sure each graphic contains 1 of the 3 pics attached (crop pic as needed); and make sure one of the graphics is all TEXT only.

Target Market(s)

men and women looking to start a business

Industry/Entity Type

Entrepreneurship

Colors
0054AA
0677BA
7BADD7
CADEEF
E8F1F8

Requirements
Must have
• All the text and use the 3 pics provided; one graphic can be all text; Simple, modern design that's easy to read

```html
<!DOCTYPE html>
<html lang="en">
<head>
<meta charset="utf-8">
<title>The Harvest Ledger Circle – Sign Up Today</title>
<link rel="stylesheet" href="https://fonts.googleapis.com/css2?family=Montserrat:wght@700;800&family=Poppins:ital,wght@1,900&display=swap">
<style>
  :root {
    --navy-deep: #06124a;
    --navy: #0a2a8a;
    --royal: #1c3fc4;
    --satin: #3a66e0;
    --band: #0677ba;
    --badge: #08142e;
    --gold: #dcc79a;
    --gold-rim: #c9b48a;
    --white: #ffffff;
    --ink: #0b1834;
  }
  html, body {
    margin: 0;
    padding: 0;
    width: 1200px;
    height: 1200px;
    overflow: hidden;
  }
  .poster {
    position: relative;
    width: 1200px;
    height: 1200px;
    overflow: hidden;
    background:
      linear-gradient(115deg, transparent 0 30%, rgba(90,130,240,.35) 38%, transparent 46%),
      linear-gradient(65deg, transparent 0 55%, rgba(90,130,240,.3) 63%, transparent 72%),
      linear-gradient(160deg, var(--royal) 0%, var(--navy) 45%, var(--navy-deep) 100%);
  }
  .signup-badge {
    position: absolute;
    left: 473px;
    top: -152px;
    width: 254px;
    height: 254px;
    border-radius: 50%;
    background: var(--badge);
    border: 4px solid var(--gold-rim);
    box-sizing: border-box;
    display: flex;
    align-items: flex-end;
    justify-content: center;
    padding-bottom: 24px;
  }
  .signup-badge span {
    font-family: "Montserrat", sans-serif;
    font-weight: 700;
    font-size: 21px;
    line-height: 1.3;
    color: var(--white);
    text-align: center;
  }
  .hosts-photo {
    position: absolute;
    left: 251px;
    top: 121px;
    width: 730px;
    height: 525px;
    border-radius: 260px 260px 0 0;
    background: linear-gradient(180deg, #2b3f6e 0%, #1d2a48 60%, #163a6a 100%);
  }
  .title-disc {
    position: absolute;
    left: 161px;
    top: 460px;
    width: 920px;
    height: 920px;
    border-radius: 50%;
    background: var(--navy);
  }
  .course-name {
    position: absolute;
    left: 161px;
    width: 920px;
    top: 522px;
    margin: 0;
    text-align: center;
    font-family: "Montserrat", sans-serif;
    font-weight: 800;
    color: var(--gold);
    line-height: 1.15;
    text-shadow: 2px 2px 0 rgba(4,10,40,.6);
  }
  .course-name .line-1 { display: block; font-size: 56px; }
  .course-name .line-2 { display: block; font-size: 64px; }
  .headline-band {
    position: absolute;
    left: 0;
    top: 748px;
    width: 1200px;
    height: 354px;
    background: var(--band);
  }
  .headline {
    position: absolute;
    left: 0;
    top: 795px;
    width: 1200px;
    margin: 0;
    text-align: center;
    font-family: "Poppins", sans-serif;
    font-style: italic;
    font-weight: 900;
    font-size: 78px;
    line-height: 90px;
    letter-spacing: -2px;
    color: var(--white);
    text-shadow: -6px 4px 0 var(--ink);
  }
  .headline span { display: block; }
</style>
</head>
<body>
  <main class="poster">
    <div class="hosts-photo" role="img" aria-label="Photo of the two course hosts, a man in a black turtleneck and a woman in a teal blazer, smiling"></div>
    <div class="title-disc"></div>
    <div class="signup-badge"><span>SIGN UP<br>TODAY</span></div>
    <h2 class="course-name">
      <span class="line-1">THE HARVEST</span>
      <span class="line-2">LEDGER CIRCLE</span>
    </h2>
    <div class="headline-band"></div>
    <h1 class="headline">
      <span>How to Launch</span>
      <span>a Multi-Million Business</span>
      <span>From Scratch</span>
    </h1>
  </main>
</body>
</html>
```